Lumavento business card

We need a modern business card - With our 4 colors - See web: www.lumavento.dk

I have attached logo and som old business Cards we have - Lets Make the new ones shine...:-) -

Industry/Entity Type

Business

Requirements
Must have
• the logo with lumavento only,

```html
<!DOCTYPE html>
<html lang="da">
<head>
<meta charset="utf-8">
<title>Lumavento – visitkort</title>
<link rel="stylesheet" href="https://fonts.googleapis.com/css2?family=Source+Sans+3:wght@400;600&display=swap">
<style>
  :root {
    --backdrop: #ebe7e4;
    --pink: #e9008a;
    --orange: #f5861f;
    --lime: #9dc43a;
    --purple: #7a1f7a;
    --white: #ffffff;
    --mist: #eeeeee;
  }
  * { box-sizing: border-box; margin: 0; padding: 0; }
  html, body {
    width: 1200px; height: 900px; overflow: hidden;
    background: var(--backdrop);
    font-family: "Source Sans 3", "Myriad Pro", sans-serif;
    color: var(--white);
  }
  .canvas { position: relative; width: 1200px; height: 900px; }

  .card { position: absolute; overflow: hidden; box-shadow: 0 6px 18px rgba(0,0,0,.15); }

  /* Contact side */
  .card--contact {
    left: 572px; top: 51px; width: 588px; height: 364px;
    background: var(--pink);
  }
  .card--contact .slice-art {
    position: absolute; left: 0; top: 0; width: 218px; height: 100%;
    background: linear-gradient(90deg, var(--mist) 0%, #f4f4f0 60%, #e3eecb 88%, var(--lime) 100%);
  }
  .details {
    position: absolute; right: 34px; top: 0; text-align: right;
  }
  .person__name { position: absolute; right: 0; top: 64px; white-space: nowrap; font-size: 22px; font-weight: 600; }
  .person__role { position: absolute; right: 0; top: 93px; white-space: nowrap; font-size: 15px; }
  .contact-list { position: absolute; right: 0; top: 162px; list-style: none; white-space: nowrap; font-size: 15px; }
  .contact-list li { display: flex; justify-content: flex-end; align-items: center; gap: 10px; height: 24px; }
  .contact-list svg { width: 13px; height: 13px; fill: var(--white); }
  .address { position: absolute; right: 0; top: 264px; white-space: nowrap; font-size: 16px; line-height: 23px; font-style: normal; }

  /* Brand side */
  .card--brand {
    left: 183px; top: 505px; width: 565px; height: 350px;
    background: var(--orange);
  }
  .card--brand .slice-art {
    position: absolute; right: 0; top: 0; width: 198px; height: 100%;
    background: linear-gradient(270deg, var(--mist) 0%, #f3f1f3 55%, #e2cfe2 86%, var(--purple) 100%);
  }
  .brand {
    position: absolute; left: 62px; top: 0; width: 257px; text-align: center;
  }
  .brand__dot {
    position: absolute; left: 103px; top: 92px; width: 52px; height: 52px;
    border-radius: 50%; background: var(--white);
  }
  .brand__name {
    position: absolute; left: 0; top: 192px; width: 100%;
    font-size: 22px; letter-spacing: 2px; font-weight: 400;
  }
  .brand__rule {
    position: absolute; left: 0; top: 232px; width: 100%; height: 3px; background: var(--white);
  }
  .brand__tagline {
    position: absolute; left: 0; top: 248px; width: 100%; font-size: 15px;
  }
</style>
</head>
<body>
<main class="canvas">

  <section class="card card--contact">
    <div class="slice-art" role="img" aria-label="Large lime citrus slice decoration"></div>
    <div class="details">
      <h1 class="person__name">Sigrid Valbjørn</h1>
      <p class="person__role">Salgsdirektor</p>
      <ul class="contact-list">
        <li>+45 60 12 34 87
          <svg viewBox="0 0 16 16" aria-hidden="true"><path d="M3.5 1l2.5 3-1.5 2c1 2 2.5 3.5 4.5 4.5l2-1.5 3 2.5-1.5 2.5C7 14 2 9 1 2.5z"/></svg>
        </li>
        <li>sv@lumavento.dk
          <svg viewBox="0 0 16 16" aria-hidden="true"><path d="M1 3h14v10H1z M2 4.5v.3l6 4 6-4v-.3z" fill-rule="evenodd"/></svg>
        </li>
        <li>www.lumavento.dk
          <svg viewBox="0 0 16 16" aria-hidden="true"><circle cx="8" cy="8" r="7"/><path d="M4 5h3l1 2-2 2 1 3-2-1-1-3zM10 3l2 2-1 2-2-1z" fill="#e9008a"/></svg>
        </li>
      </ul>
      <address class="address">Ravnsborg Allé 14 -<br>2000 Frederiksberg -Tlf. 38 41 76 02</address>
    </div>
  </section>

  <section class="card card--brand">
    <div class="brand">
      <span class="brand__dot" aria-hidden="true"></span>
      <p class="brand__name">lumavento</p>
      <span class="brand__rule" aria-hidden="true"></span>
      <p class="brand__tagline">Medier til unge</p>
    </div>
    <div class="slice-art" role="img" aria-label="Large purple citrus slice decoration"></div>
  </section>

</main>
</body>
</html>
```